Business card design Needed for new logo / Construction business, home extensions and new builds

We need a business card design using our new logo files which i will attach to this project :)

We are a small construction business specialising in home extensions, new builds and property development. We are very ambitious and would appreciate professional and elegant designs for our new business card.

Very serious about using the services on MakerQuarry and recently acquired our new logo from here :)

Please get involved, i will feedback when i can as i am very busy but can respond daily, thanks

Target Market(s)

People that want to build onto their houses, new building developments or adding too their existing property

Industry/Entity Type

Construction

Contact Information for Business Card

Renwick Tolliver Construction, Lionel Ashby (Managing Director), Tel 07822254961, email - info@renwick-tolliver, www.renwick-tolliver.co.uk

Colors

Designer to choose colors to be used in the design.

Requirements
Must have
• I like a deep grey on the back please. A lot of you have provided black from and back, try mixing things up a little. The black looks cool 😎 Thanks

```html
<!DOCTYPE html>
<html lang="en">
<head>
<meta charset="utf-8">
<title>Renwick Tolliver Construction – Business Card</title>
<link rel="stylesheet" href="https://fonts.googleapis.com/css2?family=Lato:wght@400;700;900&display=swap">
<style>
  :root {
    --canvas: #2e2e2e;
    --card-black: #1b1b1c;
    --back-grey: #202021;
    --gold-mid: #e0a934;
    --ink: #1a1a1a;
    --white: #f1f1f1;
  }
  * { margin: 0; padding: 0; box-sizing: border-box; }
  html, body { width: 1200px; height: 875px; overflow: hidden; }
  body {
    background: var(--canvas);
    font-family: "Lato", sans-serif;
    position: relative;
  }
  .card {
    position: absolute;
    width: 520px;
    height: 300px;
    border-radius: 16px;
    overflow: hidden;
    box-shadow: 0 18px 40px rgba(0,0,0,.45);
  }
  /* Back side */
  .card-back {
    left: 60px;
    top: 130px;
    background: var(--back-grey);
  }
  .back-brand {
    position: absolute;
    top: 105px;
    left: 0;
    width: 100%;
    display: flex;
    align-items: center;
    justify-content: center;
    gap: 14px;
  }
  .brand-square {
    width: 18px;
    height: 18px;
    background: var(--gold-mid);
    flex: none;
  }
  .brand-name {
    font-weight: 700;
    color: var(--gold-mid);
    font-size: 30px;
    letter-spacing: 3px;
    text-transform: uppercase;
  }
  .back-web {
    position: absolute;
    bottom: 42px;
    width: 100%;
    text-align: center;
    color: var(--white);
    font-size: 15px;
    letter-spacing: 4px;
    text-transform: uppercase;
  }
  /* Front side */
  .card-front {
    left: 620px;
    top: 445px;
    background: var(--card-black);
  }
  .card-front svg.bands { position: absolute; inset: 0; }
  .holder {
    position: absolute;
    left: 20px;
    top: 76px;
    text-align: right;
    width: 180px;
  }
  .holder-name {
    font-weight: 900;
    font-size: 24px;
    color: var(--ink);
    line-height: 1.05;
  }
  .holder-title {
    font-size: 13px;
    color: var(--ink);
    margin-top: 3px;
  }
  .divider {
    position: absolute;
    left: 214px;
    top: 32px;
    width: 1.5px;
    height: 74px;
    background: var(--ink);
  }
  .contacts {
    position: absolute;
    left: 228px;
    top: 36px;
    list-style: none;
    font-size: 12.5px;
    color: var(--ink);
  }
  .contacts li {
    display: flex;
    align-items: center;
    gap: 7px;
    height: 21px;
  }
  .contacts svg { width: 11px; height: 11px; flex: none; }
  .front-brand {
    position: absolute;
    left: 0;
    width: 100%;
    top: 212px;
    display: flex;
    align-items: center;
    justify-content: center;
    gap: 10px;
  }
  .front-brand .brand-square { width: 14px; height: 14px; }
  .front-brand .brand-name { font-size: 20px; letter-spacing: 2px; }
</style>
</head>
<body>

<section class="card card-back" aria-label="Card back">
  <div class="back-brand">
    <span class="brand-square"></span>
    <span class="brand-name">Renwick Tolliver</span>
  </div>
  <p class="back-web">www.renwick-tolliver.co.uk</p>
</section>

<section class="card card-front" aria-label="Card front">
  <svg class="bands" width="520" height="300" viewBox="0 0 520 300">
    <defs>
      <linearGradient id="goldFoil" x1="0" y1="1" x2="1" y2="0">
        <stop offset="0" stop-color="#f0b12c"/>
        <stop offset="0.25" stop-color="#c0841c"/>
        <stop offset="0.55" stop-color="#fbd98a"/>
        <stop offset="0.8" stop-color="#f3c867"/>
        <stop offset="1" stop-color="#c0841c"/>
      </linearGradient>
      <linearGradient id="silverFoil" x1="0" y1="0" x2="1" y2="0">
        <stop offset="0" stop-color="#9a9a9a"/>
        <stop offset="0.5" stop-color="#f2f2f2"/>
        <stop offset="1" stop-color="#b0b0b0"/>
      </linearGradient>
    </defs>
    <rect x="0" y="0" width="520" height="172" fill="url(#goldFoil)"/>
    <rect x="0" y="182" width="520" height="5" fill="url(#silverFoil)"/>
  </svg>

  <div class="holder">
    <p class="holder-name">Lionel Ashby</p>
    <p class="holder-title">Managing Director</p>
  </div>
  <span class="divider"></span>
  <ul class="contacts">
    <li>
      <svg viewBox="0 0 24 24" aria-hidden="true"><path fill="#1a1a1a" d="M6.6 10.8a15 15 0 0 0 6.6 6.6l2.2-2.2a1 1 0 0 1 1-.25 11.4 11.4 0 0 0 3.6.57 1 1 0 0 1 1 1V20a1 1 0 0 1-1 1A17 17 0 0 1 3 4a1 1 0 0 1 1-1h3.5a1 1 0 0 1 1 1c0 1.25.2 2.45.57 3.6a1 1 0 0 1-.25 1z"/></svg>
      07822254961
    </li>
    <li>
      <svg viewBox="0 0 24 24" aria-hidden="true"><path fill="#1a1a1a" d="M2 5h20v14H2z M2 5l10 8 10-8" stroke="#f3c867" stroke-width="1.5"/></svg>
      info@renwick-tolliver.co.uk
    </li>
    <li>
      <svg viewBox="0 0 24 24" aria-hidden="true"><circle cx="12" cy="12" r="10" fill="#1a1a1a"/><path d="M2 12h20M12 2c3 3 3 17 0 20M12 2c-3 3-3 17 0 20" stroke="#f3c867" stroke-width="1.3" fill="none"/></svg>
      renwick-tolliver.co.uk
    </li>
  </ul>

  <div class="front-brand">
    <span class="brand-square"></span>
    <span class="brand-name">Renwick Tolliver Construction</span>
  </div>
</section>

</body>
</html>
```